Business Card for Professional Photographer

I'm looking for an eye catching modern clean design that compliments my logo/ website fonts & colours.
I specialise in architecture, corporate & commercial photography so I'm marketing to professional clients rather than portrait / wedding clients.

I would prefer to not have a solid black design.

My logo brand guide is as follows :

Main front font. : Reislust
Main font colour : #fff
Slogan front font : Ubuntu Bold
Monogram front font : Venti Medium
Container colour : #fff

I need print ready files in pdf .png & .eps formats.

Included in the files below are some screen grabs as reference to font & colours etc.

```html
<!DOCTYPE html>
<html lang="en">
<head>
<meta charset="utf-8">
<title>Clear Angle – Business Card</title>
<link rel="stylesheet" href="https://fonts.googleapis.com/css2?family=Roboto:wght@400&family=Ubuntu:wght@400;700&family=Saira+Semi+Condensed:wght@600&display=swap">
<style>
  :root {
    --backdrop: #3b3b3c;
    --card: #1b1b1c;
    --gold: #c9a04a;
    --white: #f4f4f4;
  }
  * { box-sizing: border-box; margin: 0; padding: 0; }
  html, body { width: 799px; height: 1200px; overflow: hidden; }
  body {
    background: var(--backdrop);
    position: relative;
    font-family: "Roboto", sans-serif;
  }
  .card {
    position: absolute;
    left: 60px;
    width: 679px;
    height: 388px;
    background: var(--card);
    border-radius: 4px;
    box-shadow: 0 14px 30px rgba(0,0,0,.45);
  }
  .card--front { top: 150px; }
  .card--back { top: 662px; }

  /* front */
  .front-brand {
    position: absolute;
    left: 0; right: 0; top: 120px;
    display: flex; flex-direction: column; align-items: center; gap: 18px;
  }
  .brand-dot {
    width: 64px; height: 64px;
    border: 6px solid var(--gold);
    border-radius: 50%;
  }
  .front-name {
    font-family: "Ubuntu", sans-serif;
    font-weight: 400;
    font-size: 40px;
    letter-spacing: 6px;
    text-transform: uppercase;
    color: var(--gold);
  }
  .front-web {
    position: absolute;
    left: 0; right: 0; top: 318px;
    text-align: center;
    font-family: "Ubuntu", sans-serif;
    font-size: 15px;
    letter-spacing: 3px;
    color: var(--gold);
  }

  /* back */
  .person { position: absolute; left: 40px; top: 38px; }
  .person__name {
    font-family: "Saira Semi Condensed", sans-serif;
    font-weight: 600;
    font-size: 21px;
    color: var(--gold);
  }
  .person__role { font-size: 14px; color: var(--white); margin-top: 2px; }

  .contact {
    position: absolute; left: 40px; top: 210px;
    list-style: none;
    font-size: 15px; color: var(--white);
    line-height: 22px;
  }
  .contact li { display: flex; align-items: center; gap: 10px; }
  .contact svg { width: 14px; height: 14px; fill: none; stroke: var(--gold); stroke-width: 1.8; }
  .contact .address { margin-top: 2px; }

  .back-brand {
    position: absolute; right: 40px; bottom: 36px;
    display: flex; flex-direction: column; align-items: center;
  }
  .back-brand .brand-dot { width: 56px; height: 56px; border-width: 5px; margin-bottom: 14px; }
  .back-brand__name {
    font-family: "Ubuntu", sans-serif;
    font-weight: 400;
    font-size: 26px;
    letter-spacing: 5px;
    text-transform: uppercase;
    color: var(--white);
  }
  .back-brand__tagline {
    font-family: "Ubuntu", sans-serif;
    font-weight: 700;
    font-size: 10px;
    letter-spacing: 1.6px;
    color: var(--white);
    margin-top: 4px;
  }
</style>
</head>
<body>
  <section class="card card--front">
    <div class="front-brand">
      <span class="brand-dot"></span>
      <span class="front-name">Clear Angle</span>
    </div>
    <p class="front-web">www.clearangle.com.au</p>
  </section>

  <section class="card card--back">
    <div class="person">
      <p class="person__name">Marcus Hale</p>
      <p class="person__role">Photographer</p>
    </div>

    <ul class="contact">
      <li>
        <svg viewBox="0 0 16 16"><path d="M4 2 L6.5 2 L7.5 5 L5.8 6.3 Q7 9 9.7 10.2 L11 8.5 L14 9.5 L14 12 Q13 14 11 14 Q3 12 2 5 Q2 3 4 2 Z"/></svg>
        0412587306
      </li>
      <li>
        <svg viewBox="0 0 16 16"><rect x="2" y="4" width="12" height="9"/><path d="M2 4 L8 9 L14 4"/></svg>
        info@clearangle.com.au
      </li>
      <li>
        <svg viewBox="0 0 16 16"><circle cx="8" cy="8" r="6"/><path d="M2 8 H14 M8 2 Q4.5 8 8 14 M8 2 Q11.5 8 8 14"/></svg>
        www.clearangle.com.au
      </li>
      <li class="address">48 Harbour Rd Lorne Vic 3232</li>
    </ul>

    <div class="back-brand">
      <span class="brand-dot"></span>
      <span class="back-brand__name">Clear Angle</span>
      <span class="back-brand__tagline">Architecture Corporate Commercial</span>
    </div>
  </section>
</body>
</html>
```